RK Donnelly & Associates

Create a website encompassing design work already carried out for business card.
Small accounting practice, business accounting and management, superannuation, audit, taxation.

```html
<!DOCTYPE html>
<html lang="en">
<head>
<meta charset="utf-8">
<title>RK Donnelly &amp; Associates</title>
<link rel="stylesheet" href="https://fonts.googleapis.com/css2?family=Mulish:wght@400;500;600;700&display=swap">
<style>
  :root {
    --ink: #2b2b2b;
    --muted: #7a7a7a;
    --blue: #4a90d9;
    --blue-light: #6aaaf0;
    --blue-dark: #3a78c0;
    --header: #161616;
    --footer: #050505;
    --rule: #dedede;
    --white: #ffffff;
  }
  * { margin: 0; padding: 0; box-sizing: border-box; }
  html, body { width: 821px; height: 1200px; overflow: hidden; background: var(--white); }
  body { position: relative; font-family: "Mulish", sans-serif; color: var(--ink); }
  .abs { position: absolute; }

  .site-header { left: 0; top: 0; width: 821px; height: 96px;
    background: repeating-linear-gradient(135deg, #1d1d1d 0 2px, #121212 2px 4px); }
  .brand-mark { left: 126px; top: 22px; width: 26px; height: 26px; background: var(--blue-light); }
  .brand-name { left: 160px; top: 22px; width: 150px; font-size: 15px; font-weight: 600; line-height: 15px; color: var(--white); }
  .brand-tagline { left: 71px; top: 63px; width: 237px; height: 17px; background: var(--blue-light);
    color: var(--white); font-size: 6px; font-weight: 700; line-height: 17px; text-align: center; letter-spacing: .1px; }
  .main-nav { top: 49px; font-size: 11.5px; font-weight: 500; color: var(--white); }
  .main-nav.active { color: var(--blue-light); }

  .hero { left: 0; top: 96px; width: 821px; height: 342px;
    background: linear-gradient(100deg, #7d95ad 0%, #dfe6ee 30%, #eef1f4 50%, #3a4350 65%, #9fb8d4 100%); }
  .hero-dots { left: 392px; top: 420px; display: flex; gap: 3px; }
  .hero-dots span { width: 11px; height: 11px; border-radius: 50%; background: var(--white); }

  .intro-title { left: 0; top: 466px; width: 821px; text-align: center; font-size: 25px; font-weight: 500; }
  .intro-sub { left: 0; top: 499px; width: 821px; text-align: center; font-size: 15px; color: var(--blue); }
  .intro-copy { left: 125px; top: 524px; width: 571px; text-align: center; font-size: 8.5px; line-height: 15px; color: #444; }
  .intro-rule { left: 100px; top: 584px; width: 621px; height: 4px;
    background: radial-gradient(ellipse at center top, rgba(0,0,0,.08), transparent 70%); }

  .service-photo { top: 612px; width: 210px; height: 88px; }
  .service-title { top: 707px; font-size: 15.5px; color: var(--blue); font-weight: 500; }
  .service-copy { top: 730px; width: 215px; font-size: 8.5px; line-height: 14.5px; color: var(--muted); }
  .btn { top: 781px; width: 83px; height: 24px; border-radius: 3px;
    background: linear-gradient(#7ab5f2, var(--blue-dark)); color: var(--white);
    font-size: 9px; font-weight: 600; line-height: 24px; text-align: center; box-shadow: 0 1px 2px rgba(0,0,0,.25); }

  .section-rule { left: 69px; top: 837px; width: 684px; height: 1px; background: var(--rule); }
  .block-title { font-size: 14px; font-weight: 500; color: #333; }
  .block-copy { width: 300px; font-size: 8px; line-height: 13.5px; color: var(--muted); }
  .learn-more { font-size: 8px; font-weight: 600; color: var(--blue); }
  .learn-more::after { content: " \25B8"; }

  .project-photo { width: 96px; height: 68px; }
  .project-title { font-size: 11.5px; color: var(--blue); }
  .project-copy { width: 225px; font-size: 8px; line-height: 13.5px; color: #555; }
  .project-date { font-size: 8.5px; color: #666; }

  .site-footer { left: 0; top: 1116px; width: 821px; height: 84px; background: var(--footer); }
  .footer-nav { left: 73px; top: 1138px; font-size: 10.5px; font-weight: 600; color: var(--white); word-spacing: 1px; }
  .footer-copy { left: 73px; top: 1160px; font-size: 8.5px; color: #ccc; }
  .social { top: 1135px; width: 20px; height: 20px; border-radius: 50%; background: var(--white); }
</style>
</head>
<body>
  <header class="abs site-header"></header>
  <div class="abs brand-mark"></div>
  <div class="abs brand-name">RK Donnelly<br>&amp; Associates</div>
  <div class="abs brand-tagline">Accountant · Business Solutions · Management · Superannuation · Audit</div>
  <nav>
    <span class="abs main-nav active" style="left:374px">HOME</span>
    <span class="abs main-nav" style="left:432px">ABOUT</span>
    <span class="abs main-nav" style="left:492px">SERVICES</span>
    <span class="abs main-nav" style="left:564px">PROJECT</span>
    <span class="abs main-nav" style="left:637px">BLOG</span>
    <span class="abs main-nav" style="left:692px">CONTACT</span>
  </nav>

  <div class="abs hero" role="img" aria-label="Business team smiling around a meeting table"></div>
  <div class="abs hero-dots"><span></span><span></span><span></span><span></span></div>

  <h1 class="abs intro-title">RK Donnelly &amp; Associates</h1>
  <p class="abs intro-sub">Etiam est nunc venenatis in tristique eu imperdiet</p>
  <p class="abs intro-copy">Mauris vel lacus vitae felis vestibulum volutpat. Etiam est nunc, venenatis in, tristique eu, imperdiet ac, nisl. Cum sociis natoque penatibus et magnis dis parturient montes, nascetur ridiculus mus. In iaculis facilisis massa. Etiam eu urna. Sed porta. Suspendisse quam leo</p>
  <div class="abs intro-rule"></div>

  <div class="abs service-photo" style="left:76px;background:linear-gradient(120deg,#e8ecf2,#c9d6e6 60%,#5a86c8)" role="img" aria-label="Hands working with laptop and charts"></div>
  <div class="abs service-photo" style="left:307px;background:linear-gradient(120deg,#d8dcd8,#9fb8d0 50%,#e6e6e2)" role="img" aria-label="Smiling accountant seated on a sofa"></div>
  <div class="abs service-photo" style="left:539px;background:linear-gradient(120deg,#1a1a1a,#8a6e5c 55%,#d9d2c8)" role="img" aria-label="Magnifying glass over documents"></div>

  <h2 class="abs service-title" style="left:76px">Business Accounting</h2>
  <h2 class="abs service-title" style="left:308px">Accounting Practice</h2>
  <h2 class="abs service-title" style="left:540px">Audit &amp; Taxation</h2>
  <p class="abs service-copy" style="left:76px">Etiam est nunc venenatis in tristique eu imperdiet ac nisl Cum sociis natoque penatibus et magnis dis parturient montes nascetur</p>
  <p class="abs service-copy" style="left:309px">Etiam est nunc venenatis in tristique eu imperdiet ac nisl Cum sociis natoque penatibus et magnis dis parturient montes nascetur</p>
  <p class="abs service-copy" style="left:540px">Etiam est nunc venenatis in tristique eu imperdiet ac nisl Cum sociis natoque penatibus et magnis dis parturient montes nascetur</p>
  <span class="abs btn" style="left:77px">READ MORE</span>
  <span class="abs btn" style="left:308px">READ MORE</span>
  <span class="abs btn" style="left:539px">READ MORE</span>

  <div class="abs section-rule"></div>

  <h3 class="abs block-title" style="left:71px;top:866px">WHY CHOOSE US</h3>
  <p class="abs block-copy" style="left:71px;top:888px">nonummy nibh ligula pulvinar metus eget consectetuer augue nisi quis lacus Ut ac mi quis lacus mollis aliquam Curabitur iaculis tempus eros Curabitur vel mi sit amet magna malesuada ultrices</p>
  <span class="abs learn-more" style="left:71px;top:935px">LEARN MORE</span>

  <h3 class="abs block-title" style="left:71px;top:967px">HOW WE WORK</h3>
  <p class="abs block-copy" style="left:71px;top:988px;width:300px">Etiam est nunc venenatis in tristique eu imperdiet ac nisl Cum sociis natoque penatibus et magnis dis parturient montes nascetur ridiculus mus In iaculis facilisis massa Etiam eu urna Sed porta<br><span style="display:block;margin-top:3px">Suspendisse quam leo molestie sed luctus quis feugiat in pede</span></p>
  <span class="abs learn-more" style="left:72px;top:1051px">LEARN MORE</span>

  <h3 class="abs block-title" style="left:412px;top:866px">LATEST PROJECTS</h3>
  <div class="abs project-photo" style="left:414px;top:897px;background:linear-gradient(130deg,#f2f4f6,#c3d2e4 60%,#5f93cc)" role="img" aria-label="Hands reviewing printed charts"></div>
  <div class="abs project-photo" style="left:414px;top:988px;background:linear-gradient(130deg,#3a3f48,#c8ccd2 55%,#4d5a70)" role="img" aria-label="Two colleagues reviewing a report"></div>
  <h4 class="abs project-title" style="left:521px;top:894px">Morbi porta libero ullamcorper</h4>
  <p class="abs project-copy" style="left:521px;top:911px">Vivamus porttitor, g, purus nisi eleifend libero, a tempus libero lectus feugiat felis. Morbi diam mauris, viverra in, gravida eu, mattis in, ante.</p>
  <span class="abs project-date" style="left:522px;top:957px">Posted 2 hours ago</span>
  <h4 class="abs project-title" style="left:521px;top:985px">Curabitur vel mi sit amet</h4>
  <p class="abs project-copy" style="left:521px;top:1002px">Vivamus porttitor, g, purus nisi eleifend libero, a tempus libero lectus feugiat felis. Morbi diam mauris, viverra in, gravida eu, mattis in, ante.</p>
  <span class="abs project-date" style="left:522px;top:1050px">Posted 2 hours ago</span>

  <footer class="abs site-footer"></footer>
  <nav class="abs footer-nav">HOME &nbsp;| &nbsp;ABOUT &nbsp;| &nbsp;SERVICES &nbsp;| &nbsp;PROJECT &nbsp;| &nbsp;BLOG &nbsp;| &nbsp;CONTACT</nav>
  <p class="abs footer-copy">© 2014 Company Name &nbsp;All right reserved &nbsp;Term of Use</p>
  <span class="abs social" style="left:679px"></span>
  <span class="abs social" style="left:701px"></span>
  <span class="abs social" style="left:723px"></span>
</body>
</html>
```